Quiet Lanterns for the Restless Inner Mind

I would like a website designed that would be used to upload podcasts, videos and written material about mental health. Where people will be being as honest, open and truthful as they can about mental health issues.
I would like it to look calming and soothing. Inspired by Dorlac's paintings and colour schemes.

I am on Brightlane as Dr Helen Maddox - and chirpbox as drhelenmaddox

Target Market(s)

Healthcare professionals and users of services who want to think at a deeper level about the nature of mental illness

Number of Pages Required

1 page

```html
<!DOCTYPE html>
<html lang="en">
<head>
<meta charset="utf-8">
<title>Quiet Lanterns for the Restless Inner Mind</title>
<link href="https://fonts.googleapis.com/css2?family=Raleway:wght@300;400;500;600&family=Lato:wght@300;400;700&display=swap" rel="stylesheet">
<style>
:root{
  --cream:#ece8e1;
  --card:#e6e2db;
  --band:#a8bbba;
  --pine:#3f5b4f;
  --slate:#4c5a59;
  --ink:#3b4443;
  --muted:#6f7776;
  --line:#c9c4bb;
  --white:#ffffff;
}
*{box-sizing:border-box;margin:0;padding:0}
html,body{width:1200px;height:3736px;overflow:hidden}
body{position:relative;background:var(--cream);font-family:"Lato",sans-serif;color:var(--ink)}
.abs{position:absolute}
.ph{position:absolute;display:block}
.heading{font-family:"Raleway",sans-serif;font-weight:300;letter-spacing:10px;color:var(--white);font-size:44px;line-height:52px;white-space:nowrap}
.heading.dark{color:#6c7574}
.btn{position:absolute;background:var(--slate);color:var(--white);font-family:"Lato",sans-serif;font-size:12px;display:flex;align-items:center;justify-content:center;letter-spacing:.5px}
.btn.light{background:var(--cream);color:var(--muted)}
.rule{position:absolute;height:1px;background:rgba(255,255,255,.7)}
.rule.dark{background:#9aa2a1}

/* header */
.site-header{position:absolute;left:0;top:0;width:1200px;height:64px}
.brand{position:absolute;left:228px;top:20px;display:flex;align-items:center;gap:10px;font-family:"Raleway",sans-serif;font-weight:600;font-size:14px;color:var(--pine)}
.brand i{width:22px;height:22px;border-radius:50%;background:var(--pine);display:block}
.nav{position:absolute;top:26px;display:flex;gap:34px;font-size:14px;color:var(--ink)}
.site-header .nav{left:572px}

/* hero */
.hero-card{position:absolute;left:568px;top:184px;width:304px;height:356px;background:rgba(150,170,165,.82);padding:50px 30px;color:var(--white)}
.hero-card h1{font-family:"Raleway",sans-serif;font-weight:300;font-size:36px;line-height:44px}
.hero-card p{font-size:11px;line-height:16px;margin-top:18px;opacity:.9}
.hero-card .btn{position:static;width:96px;height:30px;margin-top:34px;background:var(--pine)}

/* podcasts */
.band{position:absolute;left:0;width:1200px;background:var(--band)}
.pod-card{position:absolute;top:888px;width:224px;height:334px;background:var(--card)}
.pod-card .ph{left:0;top:0;width:224px;height:148px}
.pod-card .play{position:absolute;left:10px;top:8px;width:22px;height:22px;border-radius:50%;border:2px solid #fff}
.pod-card p{position:absolute;left:12px;top:162px;width:200px;font-size:11px;line-height:16px;color:var(--muted)}
.dot{position:absolute;width:28px;height:28px;border:1px solid #fff;border-radius:50%}

/* videos */
.video h3{font-family:"Raleway",sans-serif;font-weight:400;font-size:36px;color:#5a6261;letter-spacing:1px}
.video p{font-size:12px;line-height:18px;color:var(--muted);margin-top:14px}
.video .more{font-size:12px;color:var(--ink);margin-top:6px}
.video .src{font-size:11px;color:#9aa09f;margin-top:28px}

/* articles */
.feat-cap{position:absolute;left:232px;top:2672px;width:336px;height:80px;background:rgba(70,95,90,.72);color:#fff;padding:14px 16px}
.feat-cap h4{font-size:13px;font-weight:700}
.feat-cap p{font-size:10px;line-height:14px;margin-top:6px}
.art-item{position:absolute;left:580px;width:500px;height:124px}
.art-item .ph{left:0;top:0;width:128px;height:120px}
.art-item .txt{position:absolute;left:140px;top:0;width:360px;height:120px;background:var(--cream);padding:12px 14px}
.art-item h4{font-size:13px;font-weight:700;color:var(--ink)}
.art-item p{font-size:10px;line-height:14px;color:var(--muted);margin-top:8px}

/* contact */
.field{position:absolute;left:600px;width:300px;background:#fff;border:1px solid var(--line);font-size:11px;color:#a3a8a7;padding:8px 10px}

/* footer */
.site-footer{position:absolute;left:0;top:3520px;width:1200px;height:216px;background:var(--slate);color:#fff}
.site-footer .brand{color:#fff;top:82px}
.site-footer .brand i{background:#fff}
.site-footer .nav{left:400px;top:84px;color:#fff}
.social{position:absolute;top:80px;width:26px;height:26px;border-radius:50%;border:1px solid #fff}
</style>
</head>
<body>

<header class="site-header">
  <div class="brand"><i></i>Quiet Lanterns</div>
  <nav class="nav"><span>Home</span><span>Podcasts</span><span>Blog</span><span>About</span><span>Contact</span></nav>
</header>

<section>
  <div class="ph" role="img" aria-label="Photo of a man speaking into a podcast microphone" style="left:0;top:120px;width:232px;height:500px;background:linear-gradient(160deg,#8a8f8c,#4d4a47 60%,#2f2e2d)"></div>
  <div class="ph" role="img" aria-label="Photo of a woman smiling beside a studio microphone" style="left:280px;top:100px;width:520px;height:520px;background:linear-gradient(140deg,#8e9790,#c6beb4 45%,#6f6a67)"></div>
  <div class="ph" role="img" aria-label="Photo of two women recording a podcast at a table" style="left:888px;top:128px;width:312px;height:492px;background:linear-gradient(150deg,#d9d7d3,#a9a6a2 55%,#5e5b58)"></div>
  <div class="hero-card">
    <h1>Quiet Lanterns</h1>
    <p>Honest and gentle conversations about the restless inner mind, shared by people who live it and those who care for them every day.</p>
    <div class="btn">Explore &nbsp;›</div>
  </div>
</section>

<section class="band" style="top:732px;height:608px">
  <h2 class="heading abs" style="left:232px;top:46px">PODCASTS</h2>
  <div class="rule" style="left:580px;top:74px;width:230px"></div>
  <p class="abs" style="left:232px;top:104px;width:300px;font-size:11px;line-height:15px;color:#f3f3f1">Explore our library of podcasts on honest talk about mental health and care.</p>
  <div class="btn light" style="left:832px;top:52px;width:160px;height:30px">Browse All Podcasts</div>
</section>

<article class="pod-card" style="left:-4px">
  <div class="ph" role="img" aria-label="Podcast cover photo of two hosts talking" style="background:linear-gradient(135deg,#8d8681,#5f5752)"></div>
  <p>Maya and Clara share an honest talk about recovering from suicidal thoughts. More ›</p>
</article>
<article class="pod-card" style="left:248px">
  <div class="ph" role="img" aria-label="Podcast cover artwork with headphones" style="background:linear-gradient(135deg,#3d4a4a,#1f2727)"></div><span class="play"></span>
  <p>Maya shares her journey overcoming her mental health and opens up in this latest podcast. More ›</p>
</article>
<article class="pod-card" style="left:484px">
  <div class="ph" role="img" aria-label="Podcast cover artwork with headphones and host name" style="background:linear-gradient(135deg,#4a5050,#262b2b)"></div><span class="play"></span>
  <p>Dr. Owen sits down with our new guest about his approach to patient care. Topic of the day... More ›</p>
</article>
<article class="pod-card" style="left:724px">
  <div class="ph" role="img" aria-label="Podcast cover artwork with lettering for today's talk on depression" style="background:linear-gradient(135deg,#34404a,#1c242c)"></div><span class="play"></span>
  <p>Saturday Podcast with Clara is back. Tuesday on the stigma surrounding suicide survivors. More ›</p>
</article>
<article class="pod-card" style="left:980px">
  <div class="ph" role="img" aria-label="Podcast cover photo of hosts in a studio" style="background:linear-gradient(135deg,#7d8a90,#48545a)"></div><span class="play"></span>
  <p>Maya and Clara open up about the quiet weight of anxiety at work. More ›</p>
</article>
<span class="dot" style="left:554px;top:1262px"></span>
<span class="dot" style="left:610px;top:1262px"></span>

<section>
  <h2 class="heading dark abs" style="left:232px;top:1436px">VIDEOS</h2>
  <div class="rule dark" style="left:500px;top:1464px;width:310px"></div>
  <div class="btn" style="left:824px;top:1448px;width:144px;height:30px">Browse All Videos</div>

  <div class="ph" role="img" aria-label="Video still of two people in an interview" style="left:268px;top:1528px;width:316px;height:184px;background:linear-gradient(135deg,#d4d6d6,#8a8e8f)"></div>
  <div class="abs video" style="left:628px;top:1548px;width:340px">
    <h3>Owen Hartley</h3>
    <p>We sit down to a candid discussion with depression expert Dr. Owen Hartley who talks us into a spotlight on the culture of care.</p>
    <div class="more">Learn More ›</div>
    <div class="src">Also available as Podcast</div>
  </div>
  <div class="rule dark" style="left:232px;top:1752px;width:736px;opacity:.5"></div>

  <div class="abs video" style="left:300px;top:1820px;width:300px">
    <h3>Lena Morrow</h3>
    <p>Talk show host Lena Morrow shows her new requirements on alcoholism and suicide stories in youth.</p>
    <div class="more">Learn More ›</div>
  </div>
  <div class="ph" role="img" aria-label="Video still of a podcast studio session" style="left:620px;top:1792px;width:312px;height:168px;background:linear-gradient(135deg,#6e6a62,#b09a6e 50%,#3c3a36)"></div>
  <div class="rule dark" style="left:232px;top:2000px;width:736px;opacity:.5"></div>

  <div class="ph" role="img" aria-label="Video still of two women talking on a sofa" style="left:268px;top:2048px;width:316px;height:172px;background:linear-gradient(135deg,#c9c7c2,#7e7a74)"></div>
  <div class="abs video" style="left:628px;top:2056px;width:340px">
    <h3>Iris Penhall</h3>
    <p>Today's Talk studies with Iris Penhall and our speaker comments and share their thoughts about cultural perception on suicide.</p>
    <div class="more">Learn More ›</div>
    <div class="src">Also available as Podcast</div>
  </div>
</section>

<section class="band" style="top:2352px;height:496px;overflow:hidden">
  <div class="ph" role="img" aria-label="Soft decorative background pattern" style="left:0;top:0;width:1200px;height:496px;background:radial-gradient(circle at 15% 15%,#b1c3c2,transparent 45%),radial-gradient(circle at 90% 90%,#b1c3c2,transparent 40%)"></div>
  <h2 class="heading abs" style="left:232px;top:60px">ARTICLES</h2>
  <div class="rule" style="left:570px;top:90px;width:280px"></div>
  <div class="btn light" style="left:870px;top:72px;width:112px;height:28px">View Blog</div>
</section>
<div class="ph" role="img" aria-label="Photo of a woman meditating on a yoga mat" style="left:232px;top:2500px;width:336px;height:252px;background:linear-gradient(135deg,#c5c9c6,#8e9a96)"></div>
<div class="feat-cap">
  <h4>How Healing Can Prevent Depression</h4>
  <p>Learn how a calm routine of healing can quiet the mind and reduce the weight of low moods. Read ›</p>
</div>
<div class="art-item" style="top:2500px">
  <div class="ph" role="img" aria-label="Photo of a woman with headphones" style="background:linear-gradient(135deg,#8aa5a8,#5a6f72)"></div>
  <div class="txt"><h4>Best Podcasts for Spiritual Wellbeing</h4><p>Here are our favourite podcasts for finding peace and reflection this season. Read ›</p></div>
</div>
<div class="art-item" style="top:2628px">
  <div class="ph" role="img" aria-label="Photo of a thoughtful woman in a blue sweater" style="background:linear-gradient(135deg,#b7b3ad,#6d7a86)"></div>
  <div class="txt"><h4>How To Overcome Depression and Thoughts of Suicide by Dr. Owen</h4><p>Dr. Owen shares gentle steps to ease hard days and seek help early. Read ›</p></div>
</div>
<span class="dot" style="left:554px;top:2780px"></span>
<span class="dot" style="left:610px;top:2780px"></span>

<section class="ph" role="img" aria-label="Photo of a person on a cliff at sunset above the sea" style="left:0;top:2848px;width:1200px;height:224px;background:linear-gradient(180deg,#c6c2bc,#e3d6c6 55%,#9a9a94)"></section>
<h2 class="abs" style="left:0;top:2902px;width:1200px;text-align:center;font-family:'Raleway',sans-serif;font-weight:300;font-size:24px;letter-spacing:6px;color:#fff">SUBSCRIBE TO OUR NEWSLETTER</h2>
<p class="abs" style="left:0;top:2946px;width:1200px;text-align:center;font-size:11px;color:#fff">Stay up to date with the latest content and podcasts with our newsletter</p>
<div class="abs" style="left:360px;top:2980px;width:360px;height:32px;background:rgba(255,255,255,.85);font-size:11px;color:#9aa;padding:9px 12px">Enter your email address</div>
<div class="btn" style="left:720px;top:2980px;width:120px;height:32px">Subscribe</div>

<div class="ph" role="img" aria-label="Photo of stacked stones on a beach" style="left:0;top:3072px;width:560px;height:448px;background:linear-gradient(180deg,#9fb0b4,#6e7f83 50%,#8b8a86)"></div>
<h2 class="abs" style="left:600px;top:3142px;font-family:'Raleway',sans-serif;font-weight:300;font-size:26px;letter-spacing:5px;color:#5a6261">CONTACT US</h2>
<p class="abs" style="left:600px;top:3186px;width:300px;font-size:11px;line-height:16px;color:var(--muted)">Questions or requests for our next podcast? We'd love to hear from you. Why not drop us a line?</p>
<div class="field" style="top:3240px;height:30px">Name</div>
<div class="field" style="top:3294px;height:30px">Email Address</div>
<div class="field" style="top:3350px;height:72px">Write your message here</div>
<div class="btn" style="left:600px;top:3440px;width:76px;height:28px">Send</div>

<footer class="site-footer">
  <div class="brand"><i></i>Quiet Lanterns</div>
  <nav class="nav"><span>Home</span><span>Podcasts</span><span>Blog</span><span>About</span><span>Contact</span></nav>
  <span class="social" role="img" aria-label="Brightlane" style="left:864px"></span>
  <span class="social" role="img" aria-label="chirpbox" style="left:906px"></span>
  <span class="social" role="img" aria-label="Video channel" style="left:948px"></span>
  <div class="rule" style="left:232px;top:172px;width:736px;opacity:.4"></div>
  <p class="abs" style="left:0;top:184px;width:1200px;text-align:center;font-size:11px;color:#d6dcdb">www.quietlanterns.org</p>
</footer>

</body>
</html>
```